Creation of an elegant and modern turnkey Shopify website

Hello,

We are a new company specializing in the sale of above-ground pools. We want to create a turnkey website, ideally using Shopify. For now, we need a "showcase" site, not an e-commerce platform, with four tabs:

Home Page (an overall presentation of the company)
Our Products (an overview of all the above-ground pools we sell)
Our Projects (a page inspired by Instagram to showcase photos of our future projects)
Contact (a page with all our contact information and a contact form)

We are looking to create a highly visual, elegant, and modern website with vibrant splashes of color. We will provide the text, photos (along with instructions on where to place them on each page), and all other necessary information as attachments.

Thank you in advance for your proposals!

The Brisa Lagoon Team

Target Market(s)

Targeted at Swiss customers (a translator will need to be installed for different languages)

Industry/Entity Type

Sale of customised above-ground pools

Coding

Coded - Design and coding required

Font styles to use
Sans Serif

Colors
0094D4
00A9DD
6FCCEA
C7EBF8
E9F6FB
00AB8E
00BBA5
67D7C9
C6EFE9
E9F9F6

Requirements
Must have
• A stunning, elegant and modern look
Nice to have
• Inspiration from the colors of our logo throughout the site, but in an elegant way
Should not have
• An overly classic look for swimming pool sites

```html
<!DOCTYPE html>
<html lang="en">
<head>
<meta charset="utf-8">
<title>Brisa Lagoon – Above-Ground Pools</title>
<link href="https://fonts.googleapis.com/css2?family=Poppins:wght@300;400;500&display=swap" rel="stylesheet">
<style>
:root{
  --blue:#0094D4;--blue2:#00A9DD;--blue3:#6FCCEA;--blue4:#C7EBF8;--blue5:#E9F6FB;
  --green:#00AB8E;--green2:#00BBA5;--green4:#C6EFE9;--green5:#E9F9F6;
  --ink:#111;--muted:#555;--white:#fff;
}
*{box-sizing:border-box;margin:0;padding:0}
html,body{width:1200px;height:2461px;overflow:hidden}
body{font-family:'Poppins',sans-serif;color:var(--ink);background:#fff;position:relative}
.header{height:83px;display:flex;align-items:center;padding:0 67px 0 74px}
.brand{font-size:17px;font-weight:300;color:var(--blue2);line-height:1.1;width:60px}
.nav{margin-left:auto;display:flex;align-items:center}
.nav a{font-size:12px;color:var(--ink);text-decoration:none;padding:0 17px}
.nav a.active{background:var(--blue2);color:#fff;width:85px;height:36px;display:flex;align-items:center;justify-content:center;margin-right:16px}
.search{margin-left:18px;width:226px;height:36px;border:1px solid #ccc;display:flex;align-items:center;padding:0 12px;gap:12px;font-size:12px;color:#999}
.hero{position:absolute;top:83px;left:0;width:1200px;height:457px;background:linear-gradient(120deg,#1aa6d6,#3bb6d8 55%,#2ca2c8)}
.hero-text{position:absolute;left:67px;top:112px;width:508px;color:#fff}
.hero h1{font-size:31px;font-weight:500;line-height:42px}
.hero p{font-size:13.6px;line-height:22px;margin-top:14px;text-align:justify;font-weight:300}
.btn{display:inline-block;font-size:15px;padding:0 25px;height:52px;line-height:52px;text-decoration:none}
.btn-white{background:#fff;color:var(--blue2);margin-top:25px}
.btn-blue{background:var(--blue2);color:#fff}
.btn-green{background:var(--green2);color:#fff}
.dots{position:absolute;top:414px;left:541px;display:flex;gap:12px;align-items:center}
.dots span{width:10px;height:10px;border-radius:50%;background:#fff}
.dots span.on{width:51px;height:9px;border-radius:5px;background:#ddd}
.why{position:absolute;top:548px;left:0;width:1200px;height:422px;background:linear-gradient(180deg,#d8f3f8,#c8eef4)}
.why h2{text-align:center;font-size:29px;font-weight:500;line-height:42px;margin-top:52px}
.features{display:flex;justify-content:space-between;padding:0 60px;margin-top:32px}
.feature{width:200px;text-align:center}
.icon{width:58px;height:58px;background:var(--green2);margin:0 auto 20px;display:flex;align-items:center;justify-content:center}
.feature h3{font-size:17px;font-weight:500;line-height:25px}
.feature p{font-size:12px;color:var(--muted);line-height:20px;margin:4px auto 0;max-width:184px}
.split{position:absolute;left:0;width:1200px;height:383px}
.photo{position:absolute;top:0;height:383px}
.copy{position:absolute;top:0;height:383px;padding-top:80px}
.copy h2{font-size:30px;font-weight:500;line-height:46px}
.copy p{font-size:11.8px;color:var(--muted);line-height:20px;text-align:justify;margin:16px 0 35px}
.footer{position:absolute;top:2153px;left:0;width:1200px;height:308px;background:var(--blue2);color:#fff}
.footer .col{position:absolute}
.footer h4{font-size:15px;font-weight:500;margin-bottom:10px}
.footer li{display:block;font-size:11px;color:#fff;line-height:22px;list-style:none}
.about{font-size:11px;line-height:20px;text-align:justify;width:267px;margin-top:28px}
.email{width:309px;height:40px;background:#fff;font-size:11px;color:#999;padding:0 15px;line-height:40px}
.sub{margin-top:10px;width:105px;height:36px;background:#fff;color:var(--blue2);font-size:11px;text-align:center;line-height:36px}
.social{display:flex;gap:6px;margin-top:8px}
.social span{width:26px;height:26px;border-radius:50%;background:#fff;display:flex;align-items:center;justify-content:center}
.rule{position:absolute;top:254px;left:67px;width:1066px;height:1px;background:rgba(255,255,255,.6)}
.copyright{position:absolute;top:280px;width:100%;text-align:center;font-size:11px}
</style>
</head>
<body>
<header class="header">
  <div class="brand">Brisa Lagoon</div>
  <nav class="nav">
    <a class="active" href="#">Home</a><a href="#">Our Products</a><a href="#">Our Projects</a><a href="#">Contact Us</a>
    <div class="search"><svg width="12" height="12" viewBox="0 0 12 12"><circle cx="5" cy="5" r="4" fill="none" stroke="#999" stroke-width="1.4"/><line x1="8" y1="8" x2="11" y2="11" stroke="#999" stroke-width="1.4"/></svg>Search</div>
  </nav>
</header>

<section class="hero" role="img" aria-label="Swimmer relaxing on a pink float in clear blue pool water">
  <div class="hero-text">
    <h1>Transform Your Garden with Our Premium Above-Ground Pools!</h1>
    <p>Imagine an exceptional relaxation and leisure space right in your own backyard. With our unparalleled expertise and commitment to excellence, we create above-around pools that exceed all expectations.</p>
    <a class="btn btn-white" href="#">Explore Now →</a>
  </div>
  <div class="dots"><span class="on"></span><span></span><span></span><span></span></div>
</section>

<section class="why">
  <h2>Why Choose<br>Our Above-Ground Pools?</h2>
  <div class="features">
    <div class="feature"><div class="icon"><svg width="30" height="30" viewBox="0 0 30 30" fill="none" stroke="#fff" stroke-width="1.4"><circle cx="15" cy="19" r="7"/><path d="M9 3l6 9 6-9"/></svg></div><h3>Superior Quality</h3><p>Each pool is constructed with high-quality materials, ensuring exceptional durability and strength.</p></div>
    <div class="feature"><div class="icon"><svg width="30" height="30" viewBox="0 0 30 30" fill="none" stroke="#fff" stroke-width="1.4"><rect x="4" y="4" width="22" height="22"/><path d="M9 9h8v8H9z"/></svg></div><h3>Elegant Design</h3><p>Our pools come in a variety of styles and finishes, seamlessly blending into any garden setting.</p></div>
    <div class="feature"><div class="icon"><svg width="30" height="30" viewBox="0 0 30 30" fill="none" stroke="#fff" stroke-width="1.4"><circle cx="15" cy="15" r="5"/><circle cx="15" cy="15" r="10" stroke-dasharray="3 2"/></svg></div><h3>Custom<br>and Tailor-Made</h3><p>Create the pool of your dreams with our customization options, tailored to your specific tastes and needs.</p></div>
    <div class="feature"><div class="icon"><svg width="30" height="30" viewBox="0 0 30 30" fill="none" stroke="#fff" stroke-width="1.4"><path d="M4 24h22M7 24l4-12h8l4 12M20 6l6 6"/></svg></div><h3>Easy Installation</h3><p>Enjoy your new oasis quickly with our simple and fast installation process.</p></div>
    <div class="feature"><div class="icon"><svg width="30" height="30" viewBox="0 0 30 30" fill="none" stroke="#fff" stroke-width="1.4"><path d="M15 4a7 7 0 0 0-4 13v4h8v-4a7 7 0 0 0-4-13zM12 25h6"/></svg></div><h3>Constant Innovation</h3><p>We incorporate the latest technologies to provide you with an optimal and safe swimming experience.</p></div>
  </div>
</section>

<section class="split" style="top:978px">
  <div class="photo" style="left:0;width:700px;background:linear-gradient(135deg,#4f5b66,#5e7a64)" role="img" aria-label="Wood-clad above-ground pool with glass window and waterfall on a lawn"></div>
  <div class="copy" style="left:708px;width:492px;background:var(--blue5);padding-left:67px;padding-right:67px">
    <h2>Personalized Services</h2>
    <p>We understand that every garden and client is unique. That's why we offer personalized services, from design to installation and after-sales support. Our team of experts is here to answer all your questions and guide you throughout your project.</p>
    <a class="btn btn-blue" href="#">Learn More →</a>
  </div>
</section>

<section class="split" style="top:1370px">
  <div class="copy" style="left:0;width:492px;background:var(--green5);padding:62px 67px 0">
    <h2>Guaranteed<br>Satisfaction</h2>
    <p>Your satisfaction is our top priority. We are committed to providing you with exceptional service and the highest quality products. Join our community of satisfied customers who are already enjoying their custom above-ground pools. 10-Year Warranty!</p>
    <a class="btn btn-green" href="#">Join Our Community →</a>
  </div>
  <div class="photo" style="left:500px;width:700px;background:linear-gradient(135deg,#3cbde6,#7fd6f0)" role="img" aria-label="Steel pool ladder descending into bright turquoise water beside a wooden deck"></div>
</section>

<section class="split" style="top:1762px">
  <div class="photo" style="left:0;width:700px;background:linear-gradient(135deg,#5e9a5a,#4dbcdc)" role="img" aria-label="Pool edge with chrome handrail surrounded by tropical plants"></div>
  <div class="copy" style="left:708px;width:492px;background:var(--blue5);padding-left:67px;padding-right:67px">
    <h2>Contact Us Today</h2>
    <p>Don't wait any longer to transform your garden into a wellness oasis. Contact us today to discover our range of customizable above-ground pools and get a tailored quote. Dive into a world of infinite possibilities with Brisa Lagoon.</p>
    <a class="btn btn-blue" href="#">Contact Us →</a>
  </div>
</section>

<footer class="footer">
  <div class="col" style="left:67px;top:50px">
    <div class="brand" style="color:#fff">Brisa Lagoon</div>
    <p class="about">At Brisa Lagoon, we create custom, premium above-ground pools that turn your garden into a luxurious oasis. Our high-quality materials and innovative designs ensure durability and seamless integration into any garden setting.</p>
  </div>
  <div class="col" style="left:415px;top:40px">
    <h4>Quick Links</h4>
    <ul><li>Home</li><li>Our Products</li><li>Our Projects</li><li>Contact Us</li><li>Support</li><li>Privacy Policy</li><li>Terms &amp; Condition</li></ul>
  </div>
  <div class="col" style="left:598px;top:40px">
    <h4>Contact</h4>
    <ul><li>Marco Lindqvist</li><li>Chemin des Vergers 28</li><li>1814 La Tour</li><li>079 000 12 34</li></ul>
    <h4 style="margin-top:22px">Stay Connected</h4>
    <div class="social" aria-label="Social links">
      <span><svg width="12" height="12" viewBox="0 0 12 12" fill="none" stroke="#00A9DD" stroke-width="1.2"><circle cx="6" cy="6" r="5"/><path d="M1 6h10M6 1c2 2 2 8 0 10M6 1c-2 2-2 8 0 10"/></svg></span>
      <span><svg width="12" height="12" viewBox="0 0 12 12" fill="none" stroke="#00A9DD" stroke-width="1.2"><rect x="1" y="2.5" width="10" height="7"/><path d="M1 2.5l5 4 5-4"/></svg></span>
      <span><svg width="12" height="12" viewBox="0 0 12 12" fill="none" stroke="#00A9DD" stroke-width="1.2"><path d="M1.5 2h9v6h-5l-3 2.5V8h-1z"/></svg></span>
    </div>
  </div>
  <div class="col" style="left:824px;top:32px">
    <h4>Newsletter</h4>
    <div class="email">Write your email</div>
    <div class="sub">Subscribe</div>
  </div>
  <div class="rule"></div>
  <div class="copyright">© 2024 Brisa Lagoon. All rights reserved.</div>
</footer>
</body>
</html>
```